Harbor Crestline (Business Card Design)

Need business cards designed. Something modern, chic, and sleek. Mabye the back of the card should be the navy blue that is in the logo and then just the logo on the back.

Target Market(s)

Those in the hotel, office, and renovation industry

Contact Information for Business Card

1. Logo 2. Dorian Fenwick 3. CEO/Founder 4. Phone: (833) HarbCre / (833) 427-2731 5. Email: dorian@theharborcrestline.com 6. Website: www.theharborcrestline.com

Font styles to use
Other font styles liked:
• Look at the logo font and base the font for everything else off of that.

Colors
0054AA
0677BA
7BADD7
CADEEF
E8F1F8

Requirements
Must have
• Colors that are associated in the logo
Nice to have
• Sleek modern clean and chic design.

```html
<!DOCTYPE html>
<html lang="en">
<head>
<meta charset="utf-8">
<title>Harbor Crestline — Business Card</title>
<link rel="stylesheet" href="https://fonts.googleapis.com/css2?family=Open+Sans:wght@400;600;700&display=swap">
<style>
  :root {
    --stage: #2b2b2e;
    --navy: #0c1640;
    --navy-deep: #0a1236;
    --navy-light: #1c2a6b;
    --gold: #c9a042;
    --white: #ffffff;
    --rule: rgba(255,255,255,0.55);
  }
  * { box-sizing: border-box; margin: 0; padding: 0; }
  html, body { width: 1200px; height: 780px; overflow: hidden; }
  body {
    background: var(--stage);
    font-family: "Open Sans", Arial, sans-serif;
    display: flex; align-items: center; justify-content: center; gap: 50px;
  }
  .card {
    position: relative; width: 525px; height: 300px;
    background: var(--navy); color: var(--white); overflow: hidden;
    border-radius: 4px;
    box-shadow: 0 14px 30px rgba(0,0,0,0.45);
  }
  .brand {
    display: flex; align-items: center; gap: 10px;
    font-weight: 600; letter-spacing: 0.14em; text-transform: uppercase;
    color: var(--white);
  }
  .brand-square { background: var(--white); flex: none; }

  /* front */
  .card-front .brand { position: absolute; top: 54px; left: 176px; font-size: 19px; }
  .card-front .brand-square { width: 16px; height: 16px; }
  .identity {
    position: absolute; top: 128px; left: 32px; width: 180px; text-align: right;
  }
  .person-name { font-size: 25px; font-weight: 700; line-height: 1.15; white-space: nowrap; }
  .person-first { color: var(--gold); }
  .person-role { font-size: 13px; margin-top: 4px; }
  .divider {
    position: absolute; top: 118px; left: 232px; width: 1px; height: 96px; background: var(--rule);
  }
  .contacts { position: absolute; top: 128px; left: 250px; list-style: none; font-size: 12.5px; }
  .contacts li { display: flex; align-items: center; gap: 8px; line-height: 1.9; }
  .contacts svg { width: 12px; height: 12px; flex: none; }
  .address-band {
    position: absolute; left: 0; right: 0; bottom: 22px; height: 30px;
    background: var(--gold); display: flex; align-items: center; padding-left: 32px;
    font-size: 13px; color: var(--white);
  }

  /* back */
  .card-back .pattern {
    position: absolute; inset: 0;
    background: linear-gradient(120deg, var(--navy-deep) 0%, var(--navy) 45%, var(--navy-light) 80%, #3a4680 100%);
  }
  .card-back .brand {
    position: absolute; top: 50%; left: 50%; transform: translate(-50%, -50%);
    font-size: 24px; white-space: nowrap;
  }
  .card-back .brand-square { width: 20px; height: 20px; }
</style>
</head>
<body>
  <section class="card card-front">
    <div class="brand"><span class="brand-square"></span>Harbor Crestline</div>

    <div class="identity">
      <p class="person-name"><span class="person-first">Dorian</span> Fenwick</p>
      <p class="person-role">CEO/Founder</p>
    </div>

    <span class="divider"></span>

    <ul class="contacts">
      <li>
        <svg viewBox="0 0 24 24" fill="#c9a042" aria-hidden="true"><path d="M6.6 10.8a15.1 15.1 0 0 0 6.6 6.6l2.2-2.2a1 1 0 0 1 1-.25 11.4 11.4 0 0 0 3.6.57 1 1 0 0 1 1 1V20a1 1 0 0 1-1 1A17 17 0 0 1 3 4a1 1 0 0 1 1-1h3.5a1 1 0 0 1 1 1c0 1.25.2 2.45.57 3.57a1 1 0 0 1-.25 1z"/></svg>
        (833) HarbCre / (833) 427-2731
      </li>
      <li>
        <svg viewBox="0 0 24 24" fill="none" stroke="#c9a042" stroke-width="2" aria-hidden="true"><circle cx="12" cy="12" r="9"/><path d="M3 12h18M12 3c3 3.2 3 14.8 0 18M12 3c-3 3.2-3 14.8 0 18"/></svg>
        www.theharborcrestline.com
      </li>
      <li>
        <svg viewBox="0 0 24 24" fill="none" stroke="#c9a042" stroke-width="2" aria-hidden="true"><rect x="3" y="5" width="18" height="14" rx="1"/><path d="M3 6l9 7 9-7"/></svg>
        dorian@theharborcrestline.com
      </li>
    </ul>

    <div class="address-band">4120 Linden Park Way Suite 210, Easton, MD 21601</div>
  </section>

  <section class="card card-back">
    <div class="pattern" role="img" aria-label="Faint repeating monogram pattern fading lighter toward the right edge"></div>
    <div class="brand"><span class="brand-square"></span>Harbor Crestline</div>
  </section>
</body>
</html>
```